Bloom Path! A website showcasing who I am as a person

Bloom Path started out as idea for me to better myself as a person and work on small projects that would help me grow as a person. Now I want to build a website showcasing "Bloom Path." I want the website to showcase who I am and how I have grown both professionally and personally. I can build the raw code of the website on my own but I am not really much of a designer. I am looking for a design where I can write and post blogs, articles and share my thoughts. A little about myself and the ideas and interests that I want to share
What is Bloom Path
Who I am
Background - Professional
Brand Marketing
Email Automation
Hiking
Rock Climbing
Traveling
Exercising and Transformation
"Personal Thoughts"
Hopefully this is enough information to get people started on some designs.
Work
3 page

```html
<!DOCTYPE html>
<html lang="en">
<head>
<meta charset="utf-8">
<title>Rohan Mehra — Bloom Path</title>
<link href="https://fonts.googleapis.com/css2?family=Mulish:wght@400;600;700;800&family=Open+Sans:wght@400;600&display=swap" rel="stylesheet">
<style>
  :root {
    --brand-blue: #2e6fb4;
    --nav-top: #4f8fd0;
    --nav-bottom: #1f5a9c;
    --ink: #222222;
    --muted: #666666;
    --line: #d6d6d6;
    --footer-bg: #2b2b2b;
    --footer-text: #c9c9c9;
    --white: #ffffff;
    --page: #ffffff;
  }
  * { box-sizing: border-box; margin: 0; padding: 0; }
  html, body { width: 1200px; height: 2880px; overflow: hidden; background: var(--page); }
  body { position: relative; font-family: "Open Sans", Arial, sans-serif; color: var(--ink); }

  .site-header { position: absolute; top: 0; left: 0; width: 1200px; height: 110px; }
  .brand { position: absolute; left: 121px; top: 30px; font-family: "Mulish", Arial, sans-serif; font-size: 37px; font-weight: 700; color: var(--ink); }
  .brand .first { color: var(--brand-blue); }
  .top-links { position: absolute; right: 119px; top: 20px; font-size: 14px; color: var(--muted); }
  .top-links span { margin: 0 8px; }

  .main-nav { position: absolute; top: 110px; left: 0; width: 1200px; height: 57px; background: linear-gradient(var(--nav-top), var(--nav-bottom)); display: flex; padding-left: 117px; }
  .main-nav a { color: var(--white); text-decoration: none; font-family: "Mulish", Arial, sans-serif; font-weight: 700; font-size: 15px; line-height: 57px; padding: 0 12px; border-right: 1px solid rgba(255,255,255,0.3); }
  .main-nav a:last-child { border-right: none; }

  .hero { position: absolute; top: 167px; left: 0; width: 1200px; height: 533px; }
  .hero-photo { position: absolute; inset: 0; background: radial-gradient(circle at 85% 30%, #f3d49a 0%, #c98a4a 18%, transparent 45%), linear-gradient(120deg, #6e5a4c 0%, #a88f7d 35%, #8a6a4e 60%, #4a3a2e 100%); }
  .hero-title { position: absolute; top: 185px; left: 0; width: 1200px; text-align: center; color: var(--white); font-family: "Mulish", Arial, sans-serif; font-weight: 800; font-size: 37px; line-height: 44px; text-shadow: 0 2px 6px rgba(0,0,0,0.55); text-transform: uppercase; }
  .hero-button { position: absolute; top: 294px; left: 520px; width: 172px; height: 40px; border: 2px solid var(--white); color: var(--white); font-size: 17px; text-align: center; line-height: 36px; text-transform: uppercase; }
  .slider-dots { position: absolute; top: 501px; left: 557px; display: flex; gap: 8px; }
  .slider-dots i { width: 14px; height: 14px; border-radius: 50%; background: var(--white); }
  .slider-dots i:first-child { background: transparent; border: 2px solid var(--white); }

  .section-title { position: absolute; top: 750px; left: 119px; font-family: "Mulish", Arial, sans-serif; font-size: 28px; font-weight: 400; }

  .post { position: absolute; left: 117px; width: 683px; height: 281px; border: 1px solid var(--line); }
  .post-photo { position: absolute; left: 20px; top: 20px; width: 319px; height: 234px; }
  .post-body { position: absolute; left: 357px; top: 22px; width: 310px; }
  .post-title { font-family: "Mulish", Arial, sans-serif; font-size: 20px; line-height: 25px; font-weight: 600; color: var(--brand-blue); }
  .post-date { font-size: 14px; margin: 12px 0 14px; }
  .post-excerpt { font-size: 12.5px; line-height: 19px; color: var(--muted); }
  .read-more { display: block; margin-top: 16px; font-size: 14px; text-transform: uppercase; }

  .pagination { position: absolute; top: 2327px; left: 119px; display: flex; gap: 8px; }
  .pagination span { width: 26px; height: 26px; background: #e4e4e4; color: #555; font-size: 13px; text-align: center; line-height: 26px; }
  .pagination span.current { background: var(--brand-blue); color: var(--white); }

  .sidebar-card { position: absolute; left: 822px; width: 261px; }
  .about-card { top: 791px; height: 380px; background: linear-gradient(#4e8cd0, var(--nav-bottom)); color: var(--white); text-align: center; }
  .about-card .hex { position: absolute; left: 34px; top: -42px; }
  .card-heading { font-family: "Mulish", Arial, sans-serif; font-size: 24px; font-weight: 400; }
  .about-card .card-heading { position: absolute; top: 150px; width: 100%; }
  .about-card p { position: absolute; top: 196px; left: 24px; width: 213px; font-size: 12.5px; line-height: 19px; }
  .outline-button { position: absolute; left: 70px; width: 138px; height: 34px; font-size: 14px; line-height: 30px; text-transform: uppercase; text-align: center; }
  .about-card .outline-button { top: 316px; border: 2px solid var(--white); }

  .project-card { top: 1190px; height: 429px; background: var(--white); box-shadow: 0 2px 8px rgba(0,0,0,0.15); text-align: center; }
  .project-photo { width: 261px; height: 170px; background: linear-gradient(135deg, #b7c6d3, #6a7a88 55%, #2d3a4a); }
  .project-card .card-heading { margin-top: 22px; color: var(--ink); }
  .project-card p { margin: 12px 24px 0; font-size: 12.5px; line-height: 19px; color: #888; }
  .project-card .outline-button { top: 366px; left: 62px; border: 2px solid var(--brand-blue); color: var(--brand-blue); }

  .top-articles { top: 1638px; height: 426px; background: var(--white); box-shadow: 0 2px 8px rgba(0,0,0,0.15); }
  .top-articles h3 { height: 46px; background: #111; color: var(--white); text-align: center; font-family: "Mulish", Arial, sans-serif; font-weight: 400; font-size: 23px; line-height: 46px; }
  .mini-post { position: absolute; left: 22px; display: flex; gap: 12px; }
  .mini-thumb { width: 66px; height: 66px; border-radius: 50%; flex: none; }
  .mini-post h4 { font-family: "Mulish", Arial, sans-serif; font-size: 14px; font-weight: 600; color: var(--brand-blue); }
  .mini-post p { font-size: 11.5px; line-height: 17px; color: #999; width: 140px; }
  .mini-post .read-more { margin-top: 2px; font-size: 12px; }

  .ad-slot { top: 2089px; height: 213px; background: linear-gradient(#f7de16, #f2d000); border: 1px solid #ccc; }

  .site-footer { position: absolute; top: 2434px; left: 0; width: 1200px; height: 446px; background: var(--footer-bg); color: var(--footer-text); }
  .footer-col { position: absolute; top: 74px; }
  .footer-col h5 { font-family: "Mulish", Arial, sans-serif; font-size: 20px; font-weight: 400; color: var(--white); margin-bottom: 18px; }
  .footer-col li { list-style: none; font-size: 14.5px; line-height: 26.5px; }
  .contact-field { width: 264px; height: 36px; border: 1px solid #8a8a8a; margin-bottom: 8px; font-size: 12.5px; color: var(--white); padding-left: 14px; line-height: 34px; }
  .submit { width: 142px; height: 40px; background: #3f82c8; color: var(--white); text-align: center; line-height: 40px; font-size: 15px; text-transform: uppercase; margin-top: 4px; }
  .social { display: flex; gap: 6px; }
  .social i { width: 32px; height: 32px; border: 2px solid var(--white); border-radius: 50%; }
  .footer-rule { position: absolute; top: 366px; left: 121px; width: 966px; height: 1px; background: #555; }
  .copyright { position: absolute; top: 392px; width: 1200px; text-align: center; font-size: 12.5px; color: #aaa; }
</style>
</head>
<body>
  <header class="site-header">
    <div class="brand"><span class="first">Rohan</span> Mehra</div>
    <div class="top-links">Exercising and Transformation<span>|</span>Personal Thoughts</div>
  </header>

  <nav class="main-nav">
    <a>What is Bloom Path</a><a>Who I am</a><a>Background - Professional</a><a>Brand Marketing</a><a>Email Automation</a><a>Hiking</a><a>Rock Climbing</a><a>Traveling</a>
  </nav>

  <section class="hero">
    <div class="hero-photo" role="img" aria-label="Rock climber hanging from a cliff overhang at sunset"></div>
    <h1 class="hero-title">Nullam enim leo egestas condiment<br>at laoreet mattis massa</h1>
    <div class="hero-button">Read More</div>
    <div class="slider-dots"><i></i><i></i><i></i><i></i></div>
  </section>

  <h2 class="section-title">LATSET BLOGS</h2>

  <article class="post" style="top:806px">
    <div class="post-photo" role="img" aria-label="Laptop and coffee on a wooden desk" style="background:linear-gradient(135deg,#8a6a4c,#c9b39a 50%,#5a4636)"></div>
    <div class="post-body">
      <h3 class="post-title">Suspendisse risus nibh ultricies eu volutpat non</h3>
      <div class="post-date">25 Apr 2017</div>
      <p class="post-excerpt">Maecenas aliquet velit vel turpis Mauris neque metus malesuada nec ultricies sit amet porttitor mattis enim In massa libero interdum nec interdum vel blandit sed nulla In ullamcorper est eget tempor cursus neque mi</p>
      <span class="read-more">Read More</span>
    </div>
  </article>

  <article class="post" style="top:1108px">
    <div class="post-photo" role="img" aria-label="Colleagues talking in a bright office" style="background:linear-gradient(135deg,#d9c6c4,#b88a8a 45%,#6c5a52)"></div>
    <div class="post-body">
      <h3 class="post-title">Aiverra mi eget luctus massa purus quis odio</h3>
      <div class="post-date">25 Apr 2017</div>
      <p class="post-excerpt">Maecenas aliquet velit vel turpis Mauris neque metus malesuada nec ultricies sit amet porttitor mattis enim In massa libero interdum nec interdum vel blandit sed nulla In ullamcorper est eget tempor cursus neque mi</p>
      <span class="read-more">Read More</span>
    </div>
  </article>

  <article class="post" style="top:1411px">
    <div class="post-photo" role="img" aria-label="Team sketching a brand plan on paper" style="background:linear-gradient(135deg,#e6e2dc,#b9a99a 50%,#8e7d6e)"></div>
    <div class="post-body">
      <h3 class="post-title">Maecenas aliquet velit vel turpis Mauris neque</h3>
      <div class="post-date">25 Apr 2017</div>
      <p class="post-excerpt">Maecenas aliquet velit vel turpis Mauris neque metus malesuada nec ultricies sit amet porttitor mattis enim In massa libero interdum nec interdum vel blandit sed nulla In ullamcorper est eget tempor cursus neque mi</p>
      <span class="read-more">Read More</span>
    </div>
  </article>

  <article class="post" style="top:1713px">
    <div class="post-photo" role="img" aria-label="Hand touching a tablet next to a coffee cup" style="background:linear-gradient(135deg,#d6a57a,#e9dccd 50%,#9a8676)"></div>
    <div class="post-body">
      <h3 class="post-title">Eu malesuada ut tincidunt sed diam</h3>
      <div class="post-date">25 Apr 2017</div>
      <p class="post-excerpt">Maecenas aliquet velit vel turpis Mauris neque metus malesuada nec ultricies sit amet porttitor mattis enim In massa libero interdum nec interdum vel blandit sed nulla In ullamcorper est eget tempor cursus neque mi</p>
      <span class="read-more">Read More</span>
    </div>
  </article>

  <article class="post" style="top:2020px">
    <div class="post-photo" role="img" aria-label="Wooden letter blocks on a table" style="background:linear-gradient(135deg,#7a4a2a,#c48a56 50%,#8a5a36)"></div>
    <div class="post-body">
      <h3 class="post-title">Donec convallis pede venenatis nibh Duis quam</h3>
      <div class="post-date">25 Apr 2017</div>
      <p class="post-excerpt">Maecenas aliquet velit vel turpis Mauris neque metus malesuada nec ultricies sit amet porttitor mattis enim In massa libero interdum nec interdum vel blandit sed nulla In ullamcorper est eget tempor cursus neque mi</p>
      <span class="read-more">Read More</span>
    </div>
  </article>

  <div class="pagination">
    <span>&lsaquo;</span><span class="current">1</span><span>2</span><span>3</span><span>4</span><span>5</span><span>6</span><span>&rsaquo;</span>
  </div>

  <aside>
    <div class="sidebar-card about-card">
      <svg class="hex" width="192" height="163" viewBox="0 0 192 163">
        <polygon points="47,0 145,0 192,81.5 145,163 47,163 0,81.5" fill="#ffffff"/>
        <polygon points="51,6 141,6 185,81.5 141,157 51,157 7,81.5" fill="#c9d3dc" role="img" aria-label="Portrait of the author"/>
      </svg>
      <h3 class="card-heading">Who I am</h3>
      <p>Maecenas aliquet velit vel turpis Mauris neque metus malesuada nec ultricies sit amet porttitor mattis enim In massa libero interdum nec interdum vel blandit sed</p>
      <div class="outline-button">Read More</div>
    </div>

    <div class="sidebar-card project-card">
      <div class="project-photo" role="img" aria-label="Business people discussing digital marketing at a whiteboard"></div>
      <h3 class="card-heading">What is Bloom Path</h3>
      <p>Mauris neque metus malesuada nec ultricies sit amet</p>
      <p style="margin-top:6px">Aorttitor mattis enim In massa libero interdum nec interdum vel blandit sed nulla In ullamcorper est eget tempor cursus neque mi</p>
      <div class="outline-button">Read More</div>
    </div>

    <div class="sidebar-card top-articles">
      <h3>Top Articles</h3>
      <div class="mini-post" style="top:80px">
        <div class="mini-thumb" role="img" aria-label="Idea bulb illustration" style="background:#2a9a8a"></div>
        <div><h4>Aeque consectetuer</h4><p>Praesent elementum elit at tellus Curabitur metus ipsum luctus</p><span class="read-more">Read More</span></div>
      </div>
      <div class="mini-post" style="top:206px">
        <div class="mini-thumb" role="img" aria-label="Colourful marketing graphic" style="background:#c44a7a"></div>
        <div><h4>Ut nisi erat ferm</h4><p>Praesent elementum elit at tellus Curabitu</p><span class="read-more">Read More</span></div>
      </div>
      <div class="mini-post" style="top:316px">
        <div class="mini-thumb" role="img" aria-label="Office desk scene" style="background:#a89890"></div>
        <div><h4>Curabitur iaculis</h4><p>Praesent elementum elit at tellus Curabitu</p><span class="read-more">Read More</span></div>
      </div>
    </div>

    <div class="sidebar-card ad-slot" role="img" aria-label="Advertisement banner"></div>
  </aside>

  <footer class="site-footer">
    <div class="footer-col" style="left:123px">
      <h5>Quick Links</h5>
      <ul><li>What is Bloom Path</li><li>Who I am</li><li>Background - Professional</li><li>Brand Marketing</li><li>Email Automation</li><li>Hiking</li></ul>
    </div>
    <div class="footer-col" style="left:349px">
      <h5>Resources</h5>
      <ul><li>Rock Climbing</li><li>Traveling</li><li>Exercising and Transformation</li><li>Personal Thoughts</li><li>Contact</li></ul>
    </div>
    <div class="footer-col" style="left:587px">
      <h5>Quick Contact</h5>
      <div class="contact-field">Name</div>
      <div class="contact-field">Email address</div>
      <div class="contact-field">Phone</div>
      <div class="submit">Submit</div>
    </div>
    <div class="footer-col" style="left:904px">
      <h5>Stay in Touch</h5>
      <div class="social"><i></i><i></i><i></i><i></i></div>
    </div>
    <div class="footer-rule"></div>
    <div class="copyright">© 2017 Company Name &nbsp;All right reserved &nbsp;Term of Use</div>
  </footer>
</body>
</html>
```